Im want a website LIKE VRX's and FleetHollow.com's with product payment options like Trenzo's

I need a website LIKE VRX with a header made EXACTLY LIKE THAT OF FLEETHOLLOWS .

The front page photo should be like that of FLEETHOLLOW's webpage as well.

The name of the website will be called "M.K. (Caldera Key)".

We will be targeting ALL MARKETS in a small town in central Panama and charging businesses "listing fees" like a phone book does but also providing informational blogs, news, and other interesting activities.

THIS IS A MULTI PAGE WEBSITE

THIS IS WHERE VRX's website meets Brivelle/FleetHollow.

Once the layout is built I will tweak and modify, add information, and upload items for sale.

Here is a list of specific categories that should be listed out above the front page header image/search bar

-- Home -- News -- Travel -- Activities -- Shop & Dine -- Store -- More... --

These categories should be spread across the bottom of the page in three sections:

WHATS SO GREAT ABOUT (Caldera Key),
HAND PICKED TOURS
ACTIVITIES etc.

Also lets use www.Trenzo.example 's
"HOT DESTINATIONS"
"BEAT THE BEST PRICES IN BOQUETE"
"OCTOBERS INSIDER PICKS"
"TOP DESTINATIONS"
and spread them in four sections side-by-side near the bottom of the page.

Overall I would like to see the finished product to be something LIKE VRX's and FleetHollows.

WE NEED ONLINE PAYMENT OPTIONS LIKE BRIVELLE'S WEBSITE HAS

This will be a desktop website but should be very mobile friendly as well.

-rodmund

P.S. Good luck!

If it isn't already too late to change the website name, the name of the website should be "Caldera Key". Added Friday, October 9, 2015

What do you guys think the budget should be to win this? Added Saturday, October 10, 2015

www.palmorra.example is the most amazing simple site. Whoever can make me a replica with my specifications will win immediately!!!! Added Sunday, October 18, 2015

OMG www.palmorra.example is the bomb!So simple and elegant. Whoever can make me an EXACT REPLICA OF WWW.PALMORRA.EXAMPLE as my site with the specifications mentioned in my brief will take home the $825.00 immediately! Good luck amigos! Added Sunday, October 18, 2015

Does anybody know how to add recurring monthly billing options on this website? Added Sunday, October 18, 2015

ALL MARKETS

Product

Coded - Design and coding required

5+ page

• Coinvey payment options.
• I must be able to add and remove photos/text and video from the HTML files in the page.
• Be creative my friends, and may the odds be forever in your favor!
• I added some photos of a good layout for our page below.

```html
<!DOCTYPE html>
<html lang="en">
<head>
<meta charset="utf-8">
<title>Caldera Key — Asia</title>
<link href="https://fonts.googleapis.com/css2?family=Open+Sans:wght@400;600;700&family=Lato:wght@400;700&display=swap" rel="stylesheet">
<style>
:root{
  --teal:#1aa3b3;
  --teal-dark:#138896;
  --ink:#3a3f44;
  --muted:#8a9096;
  --page:#f1f2f3;
  --card:#ffffff;
  --footer:#2b2e31;
  --footer-deep:#232628;
  --footer-text:#a4a9ad;
  --blue:#3d8fd6;
  --red:#e0533f;
  --orange:#e8742b;
  --dot:#5f7f96;
}
*{box-sizing:border-box;margin:0;padding:0}
html,body{width:729px;height:1200px;overflow:hidden}
body{font-family:"Open Sans",Arial,sans-serif;color:var(--ink);background:var(--page);position:relative}
.site{position:relative;width:729px;height:1200px}

/* header */
.hero{position:absolute;left:0;top:0;width:729px;height:121px;background:linear-gradient(180deg,#2a3846 0%,#3d5566 45%,#6c8595 100%)}
.topbar{position:absolute;top:6px;left:90px;right:90px;height:14px;display:flex;align-items:center;justify-content:space-between;font-size:6.5px;color:#d6dde2}
.social{display:flex;gap:3px}
.social span{width:9px;height:9px;border-radius:50%;background:var(--dot)}
.contact{display:flex;gap:10px}
.nav{position:absolute;top:28px;right:90px;display:flex;height:22px}
.nav a{font-size:6.8px;font-weight:700;color:#fff;text-decoration:none;padding:0 8px;line-height:22px;letter-spacing:.3px;white-space:nowrap}
.nav a.active{background:var(--teal)}
.page-title{position:absolute;left:0;top:65px;width:729px;height:56px;background:rgba(26,163,179,.88);padding:8px 90px}
.page-title h1{font-family:"Lato",sans-serif;font-weight:400;font-size:17px;color:#fff}
.page-title p{font-size:7.5px;color:#e4f5f7;margin-top:2px}

/* cards */
.tours{position:absolute;left:90px;top:165px;width:549px;display:grid;grid-template-columns:repeat(3,175px);column-gap:12px;row-gap:24px}
.card{width:175px}
.card-photo{position:relative;height:97px}
.photo-bhutan{background:linear-gradient(160deg,#7fa9c9 0%,#9b8a6a 55%,#5b6e3c 100%)}
.photo-samui{background:linear-gradient(170deg,#8fc7e0 0%,#3fa7b4 50%,#2b7c6a 100%)}
.photo-hongkong{background:linear-gradient(180deg,#c9d3dc 0%,#8a9fb1 55%,#4f6579 100%)}
.photo-tokyo{background:linear-gradient(135deg,#c5331f 0%,#e3572c 50%,#7a1c10 100%)}
.learn{position:absolute;right:6px;bottom:6px;background:var(--teal);color:#fff;font-size:6.5px;font-weight:700;padding:4px 7px}
.deal-tag{position:absolute;right:6px;top:6px;width:30px;height:30px;border-radius:50%;background:var(--red);color:#fff;font-size:5.5px;font-weight:700;text-align:center;line-height:1.2;padding-top:8px}
.card h2{font-family:"Lato",sans-serif;font-weight:400;color:var(--teal);font-size:17px;line-height:1.1;margin-top:10px;padding-right:20px}
.days{font-size:6px;color:var(--muted);margin-top:3px}
.perks{list-style:none;margin-top:8px}
.perks li{font-size:6.3px;color:#555c62;line-height:11.5px;padding-left:9px;position:relative}
.perks li::before{content:"";position:absolute;left:0;top:4px;width:4px;height:4px;background:var(--muted)}
.card-foot{display:flex;align-items:center;justify-content:space-between;margin-top:9px}
.book{background:var(--teal);color:#fff;font-size:6.8px;font-weight:700;padding:6px 9px}
.price{font-size:7.5px;font-weight:700;color:var(--ink);display:flex;align-items:center;gap:4px}
.price s{color:var(--muted);font-weight:400;font-size:6.5px}
.price .tag{width:6px;height:6px;background:var(--muted);transform:rotate(45deg)}

/* tweet band */
.tweet{position:absolute;left:0;top:822px;width:729px;height:48px;background:var(--teal);display:flex;align-items:center;padding:0 90px;gap:14px;color:#fff}
.tweet .brand{font-size:8px;font-weight:700}
.tweet p{font-size:6.5px;flex:1}
.tweet .pager{display:flex;gap:2px}
.tweet .pager span{width:12px;height:12px;border:1px solid #fff}

/* footer */
.footer{position:absolute;left:0;top:880px;width:729px;height:320px;background:var(--footer)}
.footer-cols{position:absolute;left:90px;top:24px;width:549px;display:flex;gap:20px}
.about{width:160px}
.logo{font-family:"Lato",sans-serif;font-size:15px;color:var(--orange);font-weight:400}
.about p{font-size:6px;color:var(--footer-text);line-height:9px;margin-top:8px}
.badges{display:flex;gap:8px;margin-top:12px}
.badges span{width:30px;height:24px;border-radius:50%;background:#5b6166}
.deals{width:170px}
.deals h3{font-size:8px;color:var(--teal);font-weight:600;letter-spacing:.4px;margin-bottom:10px}
.deal{display:flex;gap:7px;margin-bottom:10px}
.deal .thumb{width:26px;height:22px}
.thumb.t1{background:linear-gradient(135deg,#c9a77a,#7a5a3a)}
.thumb.t2{background:linear-gradient(135deg,#b38e5e,#5a4a3a)}
.thumb.t3{background:linear-gradient(135deg,#d8714a,#7d8fa3)}
.thumb.t4{background:linear-gradient(135deg,#8aa35a,#3e5a2c)}
.deal strong{display:block;font-size:7px;color:#fff;font-weight:600}
.deal small{font-size:5.5px;color:var(--footer-text)}
.deal small b{color:var(--red);font-weight:600}
.promos{width:170px;display:flex;flex-direction:column;gap:10px}
.promo{height:88px;position:relative;color:#fff;padding:12px 14px}
.promo.blue{background:var(--blue)}
.promo.red{background:var(--red)}
.promo .ring{position:absolute;left:14px;top:12px;width:22px;height:22px;border:2px solid #fff;border-radius:50%}
.promo .off{font-family:"Lato",sans-serif;font-size:17px;margin-left:34px;line-height:22px}
.promo .where{text-align:center;font-size:9px;margin-top:14px}
.promo .go{width:52px;margin:5px auto 0;border:1px solid #fff;font-size:5.5px;text-align:center;padding:2px 0}
.copyright{position:absolute;left:0;bottom:0;width:729px;height:26px;background:var(--footer-deep);font-size:6px;color:var(--footer-text);text-align:center;line-height:26px}
</style>
</head>
<body>
<div class="site">
  <header class="hero" role="img" aria-label="Photo of a city skyline at dusk">
    <div class="topbar">
      <div class="social"><span></span><span></span><span></span><span></span><span></span></div>
      <div class="contact"><span>hello@calderakey.example</span><span>(555) 010 4420</span></div>
    </div>
    <nav class="nav">
      <a>HOME</a><a>NEWS</a><a class="active">TRAVEL</a><a>ACTIVITIES</a><a>SHOP &amp; DINE</a><a>STORE</a><a>MORE...</a>
    </nav>
    <div class="page-title">
      <h1>Asia</h1>
      <p>Commodo ipsum fringilla felis ullamcorper</p>
    </div>
  </header>

  <main class="tours">
    <article class="card">
      <div class="card-photo photo-bhutan" role="img" aria-label="Photo of a mountain monastery in Bhutan"><span class="learn">Learn More</span></div>
      <h2>Cultural Holiday in Bhutan</h2>
      <div class="days">4 days</div>
      <ul class="perks"><li>City Tour in 3 Hours</li><li>Enjoy World Famous Restaurant</li><li>View Water Trips</li><li>Night Street Life in Downtown</li></ul>
      <div class="card-foot"><span class="book">Book Now!</span><span class="price"><i class="tag"></i>$2,000</span></div>
    </article>
    <article class="card">
      <div class="card-photo photo-samui" role="img" aria-label="Photo of limestone islands in a turquoise bay"><span class="deal-tag">Last Minute<br>20% Off</span><span class="learn">Learn More</span></div>
      <h2>Samui, Bangkok, Chiangmai</h2>
      <div class="days">6 days</div>
      <ul class="perks"><li>City Tour in 3 Hours</li><li>Enjoy World Famous Restaurant</li><li>View Water Trips</li><li>Night Street Life in Downtown</li></ul>
      <div class="card-foot"><span class="book">Book Now!</span><span class="price"><i class="tag"></i><s>$5,000</s>$4,000</span></div>
    </article>
    <article class="card">
      <div class="card-photo photo-hongkong" role="img" aria-label="Photo of the Hong Kong skyline"><span class="learn">Learn More</span></div>
      <h2>Hongkong</h2>
      <div class="days">16 June 2015 – 30 June 2015</div>
      <ul class="perks"><li>City Tour in 3 Hours</li><li>Enjoy World Famous Restaurant</li><li>View Water Trips</li><li>Night Street Life in Downtown</li></ul>
      <div class="card-foot"><span class="book">Book Now!</span><span class="price"><i class="tag"></i>$3,500</span></div>
    </article>
    <article class="card">
      <div class="card-photo photo-tokyo" role="img" aria-label="Photo of a red gate corridor in Japan"><span class="learn">Learn More</span></div>
      <h2>Tokyo, Osaka</h2>
      <div class="days">14 days</div>
      <ul class="perks"><li>City Tour in 3 Hours</li><li>Enjoy World Famous Restaurant</li><li>View Water Trips</li><li>Night Street Life in Downtown</li></ul>
      <div class="card-foot"><span class="book">Book Now!</span><span class="price"><i class="tag"></i>$1,020.00</span></div>
    </article>
  </main>

  <section class="tweet">
    <span class="brand">Chatter</span>
    <p>RT @tidewaystudio: "Working on the right thing is probably more important than working hard." – Marisol Venn — 2 days ago</p>
    <div class="pager"><span></span><span></span></div>
  </section>

  <footer class="footer">
    <div class="footer-cols">
      <div class="about">
        <div class="logo">Caldera Key</div>
        <p>Caldera Key brings local guides, listings and tours together in one place. Find trusted places to stay, eat and explore, plan your trip with ease and book every stop online.</p>
        <div class="badges"><span></span><span></span><span></span></div>
      </div>
      <div class="deals">
        <h3>LAST MINUTE DEALS</h3>
        <div class="deal"><div class="thumb t1" role="img" aria-label="Thumbnail of a European old town"></div><div><strong>Rome, Milan, Madrid</strong><small>From $1,200 · <b>$950</b></small></div></div>
        <div class="deal"><div class="thumb t2" role="img" aria-label="Thumbnail of an ancient arena"></div><div><strong>Rome City Tour</strong><small>From $800 · <b>$620</b></small></div></div>
        <div class="deal"><div class="thumb t3" role="img" aria-label="Thumbnail of a bay bridge"></div><div><strong>San Francisco</strong><small>From $1,500 · <b>$1,100</b></small></div></div>
        <div class="deal"><div class="thumb t4" role="img" aria-label="Thumbnail of a savanna landscape"></div><div><strong>Wild Life Tour</strong><small>From $2,400 · <b>$1,900</b></small></div></div>
      </div>
      <div class="promos">
        <div class="promo blue"><span class="ring"></span><div class="off">20% Off</div><div class="where">Rome, Milan, Madrid</div><div class="go">Book Now</div></div>
        <div class="promo red"><span class="ring"></span><div class="off">30% Off</div><div class="where">San Francisco</div><div class="go">Book Now</div></div>
      </div>
    </div>
    <div class="copyright">Copyright © 2015 All Rights Reserved by Caldera Key</div>
  </footer>
</div>
</body>
</html>
```